Solids Control Presentation Template Design

I'm putting together a technical 5-day course about solids control and waste management. I'm looking for an updated art and a easy on the eyes format.

```html
<!DOCTYPE html>
<html lang="en">
<head>
<meta charset="utf-8">
<title>Solids Control and Waste Management – Presentation Template</title>
<link rel="stylesheet" href="https://fonts.googleapis.com/css2?family=Lato:wght@400;700;900&family=Archivo+Black&display=swap">
<style>
:root{
  --red:#a8323a;
  --red-soft:#c9535b;
  --grey-dark:#4a4a4a;
  --grey:#8a8a8a;
  --grey-light:#c4c4c4;
  --slide-bg:#ececec;
  --header-bg:#f7f7f7;
  --page:#f4f4f4;
  --blue:#3a5fae;
  --text:#777;
}
*{box-sizing:border-box;margin:0;padding:0}
html,body{width:1200px;height:2201px;overflow:hidden;background:var(--page);font-family:'Lato',sans-serif}
.canvas{position:relative;width:1200px;height:2201px}

/* cover */
.cover{position:absolute;left:40px;top:30px;width:660px;height:371px;overflow:hidden;box-shadow:0 6px 18px rgba(0,0,0,.25)}
.cover-photo{position:absolute;inset:0;background:linear-gradient(160deg,#efd2ae 0%,#f6e4cb 45%,#fbf1e3 70%,#e6d2bb 100%)}
.cover-brand{position:absolute;left:306px;top:136px;width:300px;text-align:center}
.brand-name{font-weight:900;color:#2a2a2a;font-size:38px;letter-spacing:4px;line-height:1}
.brand-tag{color:var(--red);font-size:13px;letter-spacing:4px;font-weight:400;margin-top:3px}
.brand-services{color:#333;font-size:8.5px;letter-spacing:1.6px;margin-top:5px;font-weight:700}
.cover-title{position:absolute;left:315px;top:222px;color:var(--red);font-weight:900;font-size:25px;line-height:1.05;letter-spacing:-.3px}

/* feature list */
.features{position:absolute;left:760px;top:30px;width:430px;font-family:'Archivo Black',sans-serif;color:#111;font-size:21px;line-height:1.35}
.features li{list-style:none;position:relative;padding-left:26px;margin-bottom:2px}
.features li::before{content:"";position:absolute;left:2px;top:5px;width:17px;height:17px;border:2px solid #111;border-right:none;border-bottom-width:3px}
.features ul.sub{margin:2px 0 2px 52px}
.features ul.sub li{font-size:18px;padding-left:18px;line-height:1.3}
.features ul.sub li::before{width:7px;height:7px;border:none;background:#111;top:7px}

/* slides */
.slide{position:absolute;width:371px;height:209px;background:var(--slide-bg);overflow:hidden;box-shadow:2px 3px 6px rgba(0,0,0,.28)}
.c1{left:14px}.c2{left:417px}.c3{left:820px}
.r1{top:489px}.r2{top:773px}.r3{top:1057px}.r4{top:1341px}.r5{top:1625px}.r6{top:1909px}
.slide-head{position:absolute;left:0;top:0;width:100%;height:34px;background:var(--header-bg)}
.slide-title{position:absolute;left:22px;top:10px;font-size:13px;font-weight:700;color:var(--grey-dark);border-left:2px solid var(--grey-dark);padding-left:8px;line-height:15px}
.slide-title em{font-style:normal;color:var(--red)}
.logo{position:absolute;right:26px;top:10px;text-align:right;line-height:1}
.logo b{display:block;font-size:9px;font-weight:900;color:var(--grey-dark);letter-spacing:1.5px}
.logo span{display:block;font-size:3.6px;color:var(--red);letter-spacing:.8px;margin-top:1px}
.slide-foot{position:absolute;left:26px;right:26px;bottom:10px;height:9px;border-bottom:1px solid #d9a5a9;font-size:4.5px;font-weight:900;color:#333}
.page-no{position:absolute;right:0;bottom:1px;width:7px;height:6px;background:var(--red);color:#fff;font-size:3.5px;text-align:center;line-height:6px}
.ph{position:absolute}
.ph-rig{background:linear-gradient(135deg,#6f7e82,#3c8f94 45%,#2f5d3a 80%,#7a8c8e)}
.ph-sunset{background:linear-gradient(180deg,#e0a856,#b5702a 60%,#3b2614)}
.ph-dusk{background:linear-gradient(180deg,#8fb0d6,#3f5d86 55%,#151b26)}
.ph-mud{background:linear-gradient(135deg,#a9a39a,#76706a 50%,#c6c0b4)}
.ph-work{background:linear-gradient(135deg,#4a3a2c,#cfcfcf 50%,#3a5a3c)}
.ph-pond{background:linear-gradient(135deg,#7a4a2a,#a8835e 50%,#5d6e7a)}
.txt{font-size:4.6px;line-height:1.55;color:var(--text)}
.txt p+p{margin-top:5px}
.small-h{font-size:5px;font-weight:700;color:#333}
.bul{font-size:4.6px;color:var(--text);line-height:1.6;padding-left:6px;list-style:disc}
</style>
</head>
<body>
<div class="canvas">

  <section class="cover">
    <div class="cover-photo" role="img" aria-label="Faded photo of an oil pumpjack at sunset over flat land"></div>
    <div class="cover-brand">
      <div class="brand-name">KERNWELL</div>
      <div class="brand-tag">FIELD PROCESS SERVICES</div>
      <div class="brand-services">ENGINEERING • CONSULTING • TRAINING • EQUIPMENT</div>
    </div>
    <h1 class="cover-title">SOLIDS CONTROL AND<br>WASTE MANAGEMENT</h1>
  </section>

  <ul class="features">
    <li>Ratio 16:9</li>
    <li>Full HD</li>
    <li>Custom color pallet</li>
    <li>Custom Font -&nbsp; Easy Change</li>
    <li>Easy to edit, just drag and drop images</li>
    <li>Can be included up to 100 slides;
      <ul class="sub">
        <li>Text + images (1,2,3,4) , Text Slides</li>
        <li>Portfolio Slides , blog slides</li>
        <li>Text Slides, infographics</li>
        <li>Data Slides</li>
      </ul>
    </li>
    <li>In the sample you find 19 slides</li>
  </ul>

  <!-- Row 1 -->
  <section class="slide c1 r1">
    <div class="slide-head"></div>
    <div class="logo"><b>KERNWELL</b><span>FIELD PROCESS SERVICES</span></div>
    <div class="ph ph-dusk" style="left:26px;top:55px;width:150px;height:101px" role="img" aria-label="Silhouettes of two workers shaking hands beside a pumpjack at dusk"></div>
    <div style="position:absolute;left:190px;top:68px;border-left:2px solid var(--red);padding-left:3px">
      <div style="font-size:9px;color:var(--grey-dark);font-weight:700;line-height:1">About the Course</div>
      <div style="font-size:13px;color:var(--red);font-weight:900;line-height:1">SOLIDS CONTROL AND<br>WASTE MANAGEMENT</div>
    </div>
    <div class="txt" style="position:absolute;left:191px;top:114px;width:155px">Aim for the goal you set, and keep working each day to reach it. Stop wishing and start doing. Put in the work now and the results will follow you later.</div>
    <div class="slide-foot">SOLIDS CONTROL AND WASTE MANAGEMENT<span class="page-no">2</span></div>
  </section>

  <section class="slide c2 r1">
    <div class="slide-head"></div>
    <div class="slide-title">Agenda</div>
    <div class="logo"><b>KERNWELL</b><span>FIELD PROCESS SERVICES</span></div>
    <div style="position:absolute;left:45px;top:45px;width:310px">
      <svg width="310" height="140" viewBox="0 0 310 140">
        <g font-family="Lato,sans-serif" font-size="10" fill="#fff" text-anchor="middle">
          <rect x="0" y="2" width="26" height="20" fill="#a8323a"/><text x="13" y="15.5">01</text>
          <rect x="0" y="31" width="26" height="20" fill="#b3b3b3"/><text x="13" y="44.5">02</text>
          <rect x="0" y="60" width="26" height="20" fill="#a8323a"/><text x="13" y="73.5">03</text>
          <rect x="0" y="89" width="26" height="20" fill="#b3b3b3"/><text x="13" y="102.5">04</text>
          <rect x="0" y="118" width="26" height="20" fill="#a8323a"/><text x="13" y="131.5">05</text>
        </g>
        <g font-family="Lato,sans-serif" font-size="6.5" fill="#444">
          <text x="47" y="6">Day One</text><text x="47" y="35">Day Two</text><text x="47" y="64">Day Three</text><text x="47" y="93">Day Four</text><text x="47" y="122">Day Five</text>
        </g>
        <g font-family="Lato,sans-serif" font-size="4.4" fill="#888">
          <text x="52" y="13">• Shaker basics</text><text x="52" y="19">• Screen sizing</text><text x="130" y="13">• Mud flow review</text><text x="208" y="13">• Field notes, Q&amp;A</text>
          <text x="52" y="42">• Hydrocyclones</text><text x="52" y="48">• Cut point set</text><text x="130" y="42">• Desander setup</text><text x="208" y="42">• Wear checks</text>
          <text x="52" y="71">• Centrifuges</text><text x="52" y="77">• Bowl speeds</text><text x="130" y="71">• Polymer dosing</text><text x="208" y="71">• Case studies</text>
          <text x="52" y="100">• Waste streams</text><text x="52" y="106">• Cuttings dryers</text><text x="130" y="100">• Haul planning</text><text x="208" y="100">• Cost tracking</text>
          <text x="52" y="129">• Rules &amp; permits</text><text x="52" y="135">• Final review</text><text x="130" y="129">• Site audit</text><text x="208" y="129">• Course exam</text>
        </g>
      </svg>
    </div>
    <div class="slide-foot">SOLIDS CONTROL AND WASTE MANAGEMENT<span class="page-no">3</span></div>
  </section>

  <section class="slide c3 r1">
    <div class="slide-head"></div>
    <div class="slide-title">Course <em>Overview</em></div>
    <div class="logo"><b>KERNWELL</b><span>FIELD PROCESS SERVICES</span></div>
    <div class="txt" style="position:absolute;left:34px;top:46px;width:313px">
      <p>This course covers how drilled solids are removed from the mud system and how the waste is handled after. We start with shaker screens and move on to hydrocyclones, centrifuges and dryers. Each topic links theory to daily rig work, with clear steps crews can use on site to keep the fluid clean and costs low.</p>
      <p>Day by day you will review equipment set up, flow rates, screen choice and the cut point of each unit. We look at what goes wrong in the field and how to spot it early. Short exercises help you size a system for a given well and rate the results with simple checks.</p>
      <p>The last part of the course turns to waste: how it is stored, treated, hauled and reported. We compare methods, look at local rules and close with a site audit you can take back to your own rig and team.</p>
    </div>
    <div class="slide-foot">SOLIDS CONTROL AND WASTE MANAGEMENT<span class="page-no">4</span></div>
  </section>

  <!-- Row 2 -->
  <section class="slide c1 r2">
    <div class="slide-head"></div>
    <div class="logo"><b>KERNWELL</b><span>FIELD PROCESS SERVICES</span></div>
    <div class="ph ph-rig" style="left:0;top:55px;width:345px;height:101px" role="img" aria-label="Solids control tanks and shale shakers on a rig site"></div>
    <div style="position:absolute;left:144px;top:55px;width:201px;height:101px;background:rgba(168,50,58,.85)"></div>
    <div style="position:absolute;left:194px;top:72px;border-left:1.5px solid #fff;padding-left:3px;color:#fff">
      <div style="font-size:16px;font-weight:700;line-height:1">Introduction</div>
      <div style="font-size:9px;font-weight:900;line-height:1">SOLIDS CONTROL AND<br>WASTE MANAGEMENT</div>
    </div>
    <div class="txt" style="position:absolute;left:197px;top:120px;width:110px;color:#f1d6d8">Aim for the goal you set and keep working each day. Stop wishing and start doing now and you will reach it.</div>
    <div class="slide-foot">SOLIDS CONTROL AND WASTE MANAGEMENT<span class="page-no">7</span></div>
  </section>

  <section class="slide c2 r2">
    <div class="slide-head"></div>
    <div class="slide-title">Topic <em>Number Two</em></div>
    <div class="logo"><b>KERNWELL</b><span>FIELD PROCESS SERVICES</span></div>
    <div class="txt" style="position:absolute;left:32px;top:66px;width:152px">Shale shakers are the first line of solids removal. Screen mesh, deck angle and fluid load all change how much is taken out. Check screens often, replace torn panels fast and log the flow rate at each shift change so trends are easy to spot. A clean first stage makes every later stage work better and saves fluid, time and cost across the well.</div>
    <div class="ph ph-rig" style="left:193px;top:55px;width:150px;height:101px" role="img" aria-label="Row of shale shakers on a mud tank"></div>
    <div class="slide-foot">SOLIDS CONTROL AND WASTE MANAGEMENT<span class="page-no">6</span></div>
  </section>

  <section class="slide c3 r2">
    <div class="slide-head"></div>
    <div class="slide-title">Topic <em>Number One</em></div>
    <div class="logo"><b>KERNWELL</b><span>FIELD PROCESS SERVICES</span></div>
    <div class="ph ph-sunset" style="left:26px;top:55px;width:150px;height:101px" role="img" aria-label="Pumpjack against a golden sunset sky"></div>
    <div class="txt" style="position:absolute;left:195px;top:64px;width:152px">Drilled solids build up in the mud and raise its weight and wear on pumps. Removing them early keeps the hole stable and the rate of penetration high. This topic sets out the main terms, the size ranges of solids and how each piece of kit fits into the full system from flow line to waste pit.</div>
    <div class="slide-foot">SOLIDS CONTROL AND WASTE MANAGEMENT<span class="page-no">5</span></div>
  </section>

  <!-- Row 3 -->
  <section class="slide c1 r3">
    <div class="slide-head"></div>
    <div class="slide-title">Topic <em>Number Two</em></div>
    <div class="logo"><b>KERNWELL</b><span>FIELD PROCESS SERVICES</span></div>
    <div class="ph ph-rig" style="left:0;top:50px;width:345px;height:101px" role="img" aria-label="Wide view of solids control equipment on tanks"></div>
    <ul class="bul" style="position:absolute;left:34px;top:156px;width:100px"><li>Check screen mesh daily</li><li>Log flow at shift change</li><li>Keep decks level</li></ul>
    <ul class="bul" style="position:absolute;left:140px;top:156px;width:100px"><li>Watch cone underflow</li><li>Clear plugged inlets</li><li>Set feed pressure</li></ul>
    <ul class="bul" style="position:absolute;left:246px;top:156px;width:100px"><li>Track bowl speed</li><li>Sample mud weight</li><li>Record waste volume</li></ul>
    <div class="slide-foot">SOLIDS CONTROL AND WASTE MANAGEMENT<span class="page-no">8</span></div>
  </section>

  <section class="slide c2 r3" style="background:#6a2a30">
    <div class="ph" style="inset:0;background:linear-gradient(180deg,#8c4f55 0%,#7a3a41 50%,#5a1c22 100%)" role="img" aria-label="Pumpjack at dusk under a red tint"></div>
    <div class="slide-title" style="color:#fff;border-color:#fff;top:20px">List Sample</div>
    <div class="logo" style="top:14px"><b style="color:#fff">KERNWELL</b><span style="color:#f0c8cb">FIELD PROCESS SERVICES</span></div>
    <div class="txt" style="position:absolute;left:52px;top:50px;width:95px;color:#e7c3c6">
      <p style="border-left:1px solid #d88;padding-left:4px">Screen data shows two main trends used in the weekly review.</p>
      <p style="border-left:1px solid #d88;padding-left:4px">Cone output has two main checks done in the daily report.</p>
      <p style="border-left:1px solid #d88;padding-left:4px">Dryer output has two main checks done in the daily report.</p>
      <p style="border-left:1px solid #d88;padding-left:4px">Waste data shows two main trends used in the weekly review.</p>
      <p style="border-left:1px solid #d88;padding-left:4px">Haul logs have two main checks done in the monthly report.</p>
    </div>
    <svg style="position:absolute;left:210px;top:54px" width="14" height="130" viewBox="0 0 14 130" fill="#fff">
      <rect x="2" y="6" width="2" height="4"/><rect x="6" y="3" width="2" height="7"/><rect x="10" y="0" width="2" height="10"/>
      <circle cx="7" cy="36" r="4"/>
      <rect x="2" y="64" width="7" height="6"/><path d="M9 66l4-2v6l-4-2z"/>
      <path d="M2 98l10-4-4 10-1-4z"/>
    </svg>
    <div class="txt" style="position:absolute;left:228px;top:52px;width:100px;color:#e7c3c6">
      <p><span style="color:#fff">Statistics</span><br>A field lead is a person who runs and plans each task.</p>
      <p><span style="color:#fff">Server</span><br>A field lead is a person who runs and plans each task.</p>
      <p><span style="color:#fff">Studio</span><br>A field lead is a person who runs and plans each task.</p>
      <p><span style="color:#fff">Marketing</span><br>A field lead is a person who runs and plans each task.</p>
    </div>
  </section>

  <section class="slide c3 r3">
    <div class="slide-head"></div>
    <div class="slide-title">Bulletpoint <em>Topics</em></div>
    <div class="logo"><b>KERNWELL</b><span>FIELD PROCESS SERVICES</span></div>
    <svg style="position:absolute;left:30px;top:55px" width="320" height="120" viewBox="0 0 320 120" font-family="Lato,sans-serif">
      <g fill="#a8323a"><rect x="40" y="3" width="3" height="9" transform="rotate(40 41 7)"/><path d="M109 5h4l4-3v10l-4-3h-4z" fill="#999"/><rect x="180" y="3" width="10" height="8" rx="1" fill="#bbb"/><ellipse cx="255" cy="8" rx="6" ry="4" fill="#3a5fae"/>
      <rect x="36" y="60" width="9" height="6"/><path d="M112 58h4v3l3 6h-10l3-6z"/><path d="M180 60l8-3v10l-8-3z"/><rect x="251" y="58" width="9" height="8" fill="none" stroke="#bbb"/></g>
      <g font-size="5.5" font-weight="700" fill="#333" text-anchor="middle"><text x="40" y="24">Graphic Design</text><text x="112" y="24">Sound Design</text><text x="184" y="24">Photography</text><text x="256" y="24">Cloud Service</text>
      <text x="40" y="81">Tv Production</text><text x="112" y="81">Research</text><text x="184" y="81">Marketing</text><text x="256" y="81">Pictures</text></g>
      <g font-size="4" fill="#888" text-anchor="middle"><text x="40" y="31">Short note on this</text><text x="40" y="36">topic for the team,</text><text x="40" y="41">kept clear and brief.</text>
      <text x="112" y="31">Short note on this</text><text x="112" y="36">topic for the team,</text><text x="112" y="41">kept clear and brief.</text>
      <text x="184" y="31">Short note on this</text><text x="184" y="36">topic for the team,</text><text x="184" y="41">kept clear and brief.</text>
      <text x="256" y="31">Short note on this</text><text x="256" y="36">topic for the team,</text><text x="256" y="41">kept clear and brief.</text>
      <text x="40" y="88">Short note on this</text><text x="40" y="93">topic for the team,</text><text x="40" y="98">kept clear and brief.</text>
      <text x="112" y="88">Short note on this</text><text x="112" y="93">topic for the team,</text><text x="112" y="98">kept clear and brief.</text>
      <text x="184" y="88">Short note on this</text><text x="184" y="93">topic for the team,</text><text x="184" y="98">kept clear and brief.</text>
      <text x="256" y="88">Short note on this</text><text x="256" y="93">topic for the team,</text><text x="256" y="98">kept clear and brief.</text></g>
    </svg>
    <div class="slide-foot">SOLIDS CONTROL AND WASTE MANAGEMENT<span class="page-no">10</span></div>
  </section>

  <!-- Row 4 -->
  <section class="slide c1 r4">
    <div class="slide-head"></div>
    <div class="slide-title">Talk about <em>Text&nbsp; Topic</em></div>
    <div class="logo"><b>KERNWELL</b><span>FIELD PROCESS SERVICES</span></div>
    <div class="txt" style="position:absolute;left:30px;top:42px;width:150px">
      <p>Centrifuges take out the finest solids that shakers and cones let pass. Bowl speed, feed rate and pond depth set the cut point. Run too fast and wear climbs; run too slow and fine solids stay in the mud. Good records help crews find the right balance for each fluid type and well section over time.</p>
      <p>Dewatering units join the centrifuge to clean water for reuse. Polymer dosing must be set with care and checked with simple jar tests before each run so the flocs form well and settle out fast.</p>
    </div>
    <div class="txt" style="position:absolute;left:188px;top:42px;width:150px">
      <p>Keep spare parts on site and plan wear checks ahead of time so no unit is down when it is needed most.</p>
      <p>Weighted muds need extra care. Barite is valuable and should be kept in the system while drilled solids are removed. Two stage set ups can do this well when each stage is tuned and sampled on a fixed plan. Share results with the mud engineer each day so both teams work from the same data.</p>
      <p>Close each well with a short review of what worked and what to change next time.</p>
    </div>
    <div class="slide-foot">SOLIDS CONTROL AND WASTE MANAGEMENT<span class="page-no">11</span></div>
  </section>

  <section class="slide c2 r4">
    <div class="slide-head"></div>
    <div class="slide-title">Topic <em>Number</em></div>
    <div class="logo"><b>KERNWELL</b><span>FIELD PROCESS SERVICES</span></div>
    <div class="txt" style="position:absolute;left:32px;top:43px;width:312px">
      <p>Waste from the rig comes as wet cuttings, spent fluid and wash water. Each stream needs its own plan for storage and treatment. Dryers can cut the liquid left on cuttings and return fluid to the system, which lowers both haul volume and the cost of new mud.</p>
      <p>Sampling at each step shows how well the plan works. Test oil on cuttings, water content and solids so you can report with confidence and adjust the process where the results fall short.</p>
    </div>
    <div class="ph ph-mud" style="left:27px;top:113px;width:101px;height:61px" role="img" aria-label="Close view of wet cuttings on a screen"></div>
    <div class="ph ph-work" style="left:135px;top:113px;width:101px;height:61px" role="img" aria-label="Worker in gloves handling a sample tray"></div>
    <div class="ph ph-pond" style="left:243px;top:113px;width:101px;height:61px" role="img" aria-label="Waste pit with muddy water"></div>
    <div class="slide-foot">SOLIDS CONTROL AND WASTE MANAGEMENT<span class="page-no">13</span></div>
  </section>

  <section class="slide c3 r4">
    <div class="slide-head"></div>
    <div class="slide-title">The Process <em>We talk about</em></div>
    <div class="logo"><b>KERNWELL</b><span>FIELD PROCESS SERVICES</span></div>
    <div style="position:absolute;left:0;top:47px;width:153px;height:65px;background:#b0b0b0"></div>
    <div style="position:absolute;left:0;top:50px;width:153px;text-align:center;color:#fff;font-size:9px;font-weight:700;top:58px">Process Steps</div>
    <div class="txt" style="position:absolute;left:20px;top:72px;width:113px;color:#eee;text-align:center">Each step in the flow is shown here in a short line so the team can follow it.</div>
    <div class="ph ph-sunset" style="left:155px;top:47px;width:69px;height:65px" role="img" aria-label="Pumpjack at sunset"></div>
    <div class="ph ph-rig" style="left:226px;top:47px;width:69px;height:65px" role="img" aria-label="Shaker deck on a tank"></div>
    <div class="ph ph-mud" style="left:297px;top:47px;width:74px;height:65px" role="img" aria-label="Cuttings on a screen"></div>
    <div style="position:absolute;left:0;top:114px;width:84px;height:65px;background:#4a4a4a"></div>
    <div class="ph ph-work" style="left:86px;top:114px;width:69px;height:65px" role="img" aria-label="Worker taking a sample"></div>
    <div class="ph ph-pond" style="left:157px;top:114px;width:69px;height:65px" role="img" aria-label="Waste pit"></div>
    <div style="position:absolute;left:228px;top:114px;width:69px;height:65px;background:var(--blue)"></div>
    <div style="position:absolute;left:232px;top:116px;color:#fff;font-size:12px;font-weight:900">&ldquo;</div>
    <div class="txt" style="position:absolute;left:242px;top:120px;width:50px;color:#dfe6f5;font-size:4px">A short quote from a crew lead on how the new flow cut waste haul on site.</div>
    <div class="ph ph-dusk" style="left:299px;top:114px;width:72px;height:65px" role="img" aria-label="Silhouettes of two workers by a pumpjack"></div>
    <div class="slide-foot">SOLIDS CONTROL AND WASTE MANAGEMENT<span class="page-no">14</span></div>
  </section>

  <!-- Row 5 -->
  <section class="slide c1 r5">
    <div class="slide-head"></div>
    <div class="slide-title">Text <em>and Bullets</em></div>
    <div class="logo"><b>KERNWELL</b><span>FIELD PROCESS SERVICES</span></div>
    <div class="txt" style="position:absolute;left:30px;top:42px;width:315px">Good solids control starts with a clear plan for each well section. Set targets for mud weight and solids content, pick the right screens and check the results often. Small changes made early save large costs later on. Share data across shifts so every crew knows the state of the system and what to watch next. Keep the waste plan in step with the drilling plan so storage and haul are ready before they are needed.</div>
    <svg style="position:absolute;left:108px;top:102px" width="240" height="80" viewBox="0 0 240 80" font-family="Lato,sans-serif">
      <g fill="#a8323a"><circle cx="8" cy="10" r="8"/><circle cx="8" cy="39" r="8"/><circle cx="8" cy="67" r="8"/></g>
      <g fill="#fff"><circle cx="8" cy="10" r="3.5"/><rect x="5" y="37" width="6" height="4"/><path d="M5 70v-5h2l2-3v8z"/></g>
      <g font-size="5" font-weight="700" fill="#333"><text x="24" y="6">Factor Number One</text><text x="24" y="35">Factor Number Two</text><text x="24" y="63">Factor Number Three</text></g>
      <g font-size="4" fill="#888"><text x="24" y="12">Short note on this factor and how it shapes the daily plan for the crew on site.</text><text x="24" y="17">Keep it brief.</text>
      <text x="24" y="41">Short note on this factor and how it shapes the daily plan for the crew on site.</text><text x="24" y="46">Keep it brief.</text>
      <text x="24" y="69">Short note on this factor and how it shapes the daily plan for the crew on site.</text><text x="24" y="74">Keep it brief.</text></g>
    </svg>
    <div class="slide-foot">SOLIDS CONTROL AND WASTE MANAGEMENT<span class="page-no">12</span></div>
  </section>

  <section class="slide c2 r5">
    <div class="slide-head"></div>
    <div class="slide-title">Infographic <em>Slides</em></div>
    <div class="logo"><b>KERNWELL</b><span>FIELD PROCESS SERVICES</span></div>
    <div class="small-h" style="position:absolute;left:28px;top:58px">Analysis of the Chart</div>
    <div class="txt" style="position:absolute;left:28px;top:66px;width:145px">This chart compares solids removed across four stages. Each band shows the share taken out per stage, so you can see where the system works best and where it needs work. Use it in the weekly review to plan screen changes and set new targets for the crew on each shift.</div>
    <svg style="position:absolute;left:185px;top:58px" width="170" height="95" viewBox="0 0 170 95" font-family="Lato,sans-serif">
      <g font-size="5" fill="#888" text-anchor="end"><text x="8" y="5">6</text><text x="8" y="18">5</text><text x="8" y="31">4</text><text x="8" y="44">3</text><text x="8" y="57">2</text><text x="8" y="70">1</text><text x="8" y="83">0</text></g>
      <path d="M14 81V38L56 56 100 44 155 30V81Z" fill="#a8323a"/>
      <path d="M14 81V52L56 24 100 58 155 16V81Z" fill="#bdbdbd"/>
      <line x1="14" y1="81" x2="155" y2="81" stroke="#bbb" stroke-width=".5"/>
      <g font-size="5" fill="#888" text-anchor="middle"><text x="20" y="91">Category 1</text><text x="60" y="91">Category 2</text><text x="100" y="91">Category 3</text><text x="140" y="91">Category 4</text></g>
    </svg>
    <div class="slide-foot">SOLIDS CONTROL AND WASTE MANAGEMENT<span class="page-no">17</span></div>
  </section>

  <section class="slide c3 r5">
    <div class="slide-head"></div>
    <div class="slide-title">Analytics <em>Three Facts</em></div>
    <div class="logo"><b>KERNWELL</b><span>FIELD PROCESS SERVICES</span></div>
    <svg style="position:absolute;left:28px;top:62px" width="330" height="100" viewBox="0 0 330 100" font-family="Lato,sans-serif">
      <g font-size="6" fill="#777" text-anchor="end"><text x="36" y="7">Category 4</text><text x="36" y="26">Category 3</text><text x="36" y="45">Category 2</text><text x="36" y="64">Category 1</text></g>
      <g fill="#cfcfcf"><rect x="42" y="1" width="108" height="8"/><rect x="42" y="20" width="108" height="8"/><rect x="42" y="39" width="108" height="8"/><rect x="42" y="58" width="108" height="8"/></g>
      <g fill="#a8323a"><rect x="42" y="1" width="38" height="8"/><rect x="42" y="20" width="44" height="8"/><rect x="42" y="39" width="30" height="8"/><rect x="42" y="58" width="54" height="8"/></g>
      <g font-size="5" fill="#888" text-anchor="middle"><text x="42" y="78">0%</text><text x="60" y="78">20%</text><text x="78" y="78">40%</text><text x="96" y="78">60%</text><text x="114" y="78">80%</text><text x="133" y="78">100%</text></g>
      <circle cx="177" cy="8" r="9" fill="#a8323a"/><circle cx="177" cy="8" r="4" fill="#fff"/>
      <circle cx="177" cy="39" r="9" fill="#b3b3b3"/><rect x="173" y="36" width="8" height="6" fill="#fff"/>
      <circle cx="177" cy="68" r="9" fill="#b3b3b3"/><path d="M173 72v-6h2l3-4v10z" fill="#fff"/>
      <g font-size="5" font-weight="700" fill="#333"><text x="192" y="4">Factor Number One</text><text x="192" y="35">Factor Number Two</text><text x="192" y="64">Factor Number Three</text></g>
      <g font-size="4" fill="#888"><text x="192" y="10">Short note on this fact and what</text><text x="192" y="15">it means for the crew.</text>
      <text x="192" y="41">Short note on this fact and what</text><text x="192" y="46">it means for the crew.</text>
      <text x="192" y="70">Short note on this fact and what</text><text x="192" y="75">it means for the crew.</text></g>
    </svg>
    <div class="slide-foot">SOLIDS CONTROL AND WASTE MANAGEMENT<span class="page-no">16</span></div>
  </section>

  <!-- Row 6 -->
  <section class="slide c1 r6">
    <div class="slide-head"></div>
    <div class="slide-title">Analytics <em>Three Facts</em></div>
    <div class="logo"><b>KERNWELL</b><span>FIELD PROCESS SERVICES</span></div>
    <svg style="position:absolute;left:18px;top:44px" width="340" height="100" viewBox="0 0 340 100" font-family="Lato,sans-serif">
      <circle cx="46" cy="50" r="46" fill="#b8b8b8" opacity=".95"/>
      <circle cx="126" cy="50" r="46" fill="#d77c7f" opacity=".92"/>
      <circle cx="206" cy="50" r="46" fill="#a9a9a9" opacity=".92"/>
      <circle cx="286" cy="50" r="46" fill="#c9353d" opacity=".95"/>
      <g fill="none" stroke="#fff" stroke-width="1.5"><rect x="38" y="24" width="16" height="12" rx="1"/><rect x="118" y="24" width="16" height="12" rx="1"/><path d="M199 24l14 14M213 24l-14 14"/><path d="M280 34l10-10v16z"/></g>
      <g font-size="6.5" fill="#fff" text-anchor="middle"><text x="46" y="52">Photography</text><text x="126" y="52">Web Server</text><text x="206" y="52">Web Design</text><text x="286" y="52">Promotion</text></g>
      <g font-size="4.5" fill="#f3f3f3" text-anchor="middle"><text x="46" y="60">Short note on this</text><text x="46" y="66">item for the crew</text><text x="46" y="72">kept brief</text>
      <text x="126" y="60">Short note on this</text><text x="126" y="66">item for the crew</text><text x="126" y="72">kept brief</text>
      <text x="206" y="60">Short note on this</text><text x="206" y="66">item for the crew</text><text x="206" y="72">kept brief</text>
      <text x="286" y="60">Short note on this</text><text x="286" y="66">item for the crew</text><text x="286" y="72">kept brief</text></g>
    </svg>
    <div class="txt" style="position:absolute;left:34px;top:154px;width:310px">These four areas shape how the course material is shared with crews and clients. Each one plays a part in making field data clear, easy to find and ready for use in the next well plan.</div>
    <div class="slide-foot">SOLIDS CONTROL AND WASTE MANAGEMENT<span class="page-no">18</span></div>
  </section>

  <section class="slide c2 r6">
    <div class="slide-head"></div>
    <div class="slide-title">Elements <em>Comparison Chart</em></div>
    <div class="logo"><b>KERNWELL</b><span>FIELD PROCESS SERVICES</span></div>
    <svg style="position:absolute;left:28px;top:52px" width="320" height="100" viewBox="0 0 320 100" font-family="Lato,sans-serif">
      <g fill="none" stroke-width="2">
        <path d="M36 4a32 32 0 0 1 0 64" stroke="#a8323a"/><path d="M36 68a32 32 0 0 1 0-64" stroke="#3a5fae"/>
        <path d="M114 4a32 32 0 0 1 0 64" stroke="#3a5fae"/><path d="M114 68a32 32 0 0 1 0-64" stroke="#a8323a"/>
        <path d="M202 4a32 32 0 0 1 0 64" stroke="#a8323a"/><path d="M202 68a32 32 0 0 1 0-64" stroke="#3a5fae"/>
        <path d="M282 4a32 32 0 0 1 0 64" stroke="#3a5fae"/><path d="M282 68a32 32 0 0 1 0-64" stroke="#a8323a"/>
      </g>
      <rect x="28" y="28" width="16" height="16" rx="3" fill="#a8323a"/>
      <circle cx="114" cy="36" r="8" fill="#b3b3b3"/>
      <path d="M195 40l6-10 7 10z" fill="#b3b3b3"/>
      <rect x="274" y="28" width="16" height="16" rx="3" fill="none" stroke="#a8323a" stroke-width="2"/>
      <g font-size="5" font-weight="700" fill="#333" text-anchor="middle"><text x="36" y="86">ELEMENT ONE</text><text x="114" y="86">ELEMENT TWO</text><text x="202" y="86">ELEMENT THREE</text><text x="282" y="86">ELEMENT FOUR</text></g>
      <g font-size="3.8" fill="#888" text-anchor="middle"><text x="36" y="92">Short note on this item,</text><text x="36" y="97">kept brief.</text>
      <text x="114" y="92">Short note on this item,</text><text x="114" y="97">kept brief.</text>
      <text x="202" y="92">Short note on this item,</text><text x="202" y="97">kept brief.</text>
      <text x="282" y="92">Short note on this item,</text><text x="282" y="97">kept brief.</text></g>
    </svg>
    <div class="txt" style="position:absolute;left:34px;top:162px;width:310px">Compare the four elements side by side to see which fits the well plan best, then note the choice in the weekly report for the team.</div>
    <div class="slide-foot">SOLIDS CONTROL AND WASTE MANAGEMENT<span class="page-no">19</span></div>
  </section>

  <section class="slide c3 r6">
    <div class="ph" style="inset:0;background:linear-gradient(180deg,#dcdcdc,#c9c9c9 60%,#bdbdbd)" role="img" aria-label="Faded grey photo of a drilling rig derrick"></div>
    <div class="logo" style="top:16px"><b>KERNWELL</b><span>FIELD PROCESS SERVICES</span></div>
    <div style="position:absolute;left:0;top:150px;width:100%;height:48px;background:var(--red)"></div>
    <div style="position:absolute;left:30px;top:166px;color:#fff;font-size:13px;font-weight:700;border-left:2px solid #fff;padding-left:4px;line-height:15px">Break Time</div>
  </section>

</div>
</body>
</html>
```